Business Card Design Project

Business Card
We are rebranding with a new logo
Industry/Entity Type
Business
Contact Information for Business Card
Dennis Morvale +61 487215963 dennis@quorv.com.au P.O. Box 872 Fernlow QLD 4309
Requirements
Must have
- Logo

```html
<!DOCTYPE html>
<html lang="en">
<head>
<meta charset="utf-8">
<title>Quorv International – Business Card</title>
<link href="https://fonts.googleapis.com/css2?family=Josefin+Sans:wght@300;400;600&display=swap" rel="stylesheet">
<style>
  :root {
    --backdrop: #cfd8e2;
    --card-top: #f6f8fa;
    --card-bottom: #e3e9ef;
    --navy-light: #2d6197;
    --navy-deep: #16344f;
    --ink: #22303c;
    --contact: #b9c9db;
  }
  * { margin: 0; padding: 0; box-sizing: border-box; }
  html, body { width: 1200px; height: 899px; overflow: hidden; }
  body {
    background: var(--backdrop);
    font-family: "Josefin Sans", sans-serif;
    position: relative;
  }
  .business-card {
    position: absolute;
    left: 100px; top: 164px;
    width: 1000px; height: 571px;
    background: linear-gradient(180deg, var(--card-top), var(--card-bottom));
    overflow: hidden;
    box-shadow: 0 14px 40px rgba(20, 40, 60, 0.22);
  }
  .lower-band { position: absolute; inset: 0; width: 100%; height: 100%; }
  .brand-block {
    position: absolute;
    left: 46px; top: 128px;
    color: var(--ink);
    font-weight: 600;
    text-transform: uppercase;
  }
  .brand-name {
    display: block;
    font-size: 76px;
    line-height: 1;
    letter-spacing: 3px;
  }
  .brand-tagline {
    display: block;
    margin-top: 14px;
    font-size: 26px;
    letter-spacing: 4px;
  }
  .holder-name {
    position: absolute;
    right: 52px; top: 382px;
    font-size: 29px; font-weight: 300;
    letter-spacing: 1px;
    color: var(--contact);
    text-transform: uppercase;
  }
  .contact-list {
    position: absolute;
    right: 52px; top: 448px;
    list-style: none;
    text-align: right;
    color: var(--contact);
    font-size: 21px; font-weight: 300;
  }
  .contact-list li {
    display: flex; justify-content: flex-end; align-items: center;
    gap: 12px; height: 29px;
  }
  .contact-icon { width: 20px; height: 20px; fill: none; stroke: var(--contact); stroke-width: 1.6; }
  .postal-address {
    position: absolute;
    left: 44px; top: 480px;
    font-size: 21px; font-weight: 300;
    color: var(--contact);
  }
</style>
</head>
<body>
  <article class="business-card">
    <svg class="lower-band" viewBox="0 0 1000 571" preserveAspectRatio="none" role="img" aria-label="Decorative curved band in blue tones across the lower card">
      <defs>
        <linearGradient id="bandFill" x1="0" y1="0" x2="1" y2="0">
          <stop offset="0" stop-color="#2d6197"/>
          <stop offset="1" stop-color="#16344f"/>
        </linearGradient>
      </defs>
      <path d="M0,345 C280,410 600,380 1000,80 L1000,571 L0,571 Z" fill="url(#bandFill)"/>
    </svg>

    <h1 class="brand-block">
      <span class="brand-name">Quorv</span>
      <span class="brand-tagline">International</span>
    </h1>

    <p class="holder-name">Dennis Morvale</p>

    <ul class="contact-list">
      <li>+61 487215963
        <svg class="contact-icon" viewBox="0 0 20 20"><path d="M5 2 L8 6 L6 8 C7 11 9 13 12 14 L14 12 L18 15 L16 18 C9 17 3 11 2 4 Z"/></svg>
      </li>
      <li>dennis@quorv.com.au
        <svg class="contact-icon" viewBox="0 0 20 20"><rect x="2" y="4" width="16" height="12"/><path d="M2 4 L10 11 L18 4"/></svg>
      </li>
      <li>www.quorv.com.au
        <svg class="contact-icon" viewBox="0 0 20 20"><circle cx="10" cy="10" r="8"/><ellipse cx="10" cy="10" rx="3.5" ry="8"/><path d="M2 10 H18"/></svg>
      </li>
    </ul>

    <p class="postal-address">P.O. Box 872 Fernlow QLD 4309</p>
  </article>
</body>
</html>
```